Poster for our band

We need a logo and poster designing for us to send to the venues we are performing at. Our band is called "Brisk"
Can use different backgrounds to make poster look more Arty
We would like the poster to look contemporary, modern and unique. As many or as little pictures can be used that I will send.
We perform at Holiday Parks, Hotels etc so the Poster needs to look classy and sophisticated.Can be Portrait or Landscape. Poster could be Black and White or Colour
A very creative Logo
Could contain the following script somewhere on the poster.

Performing hits by- The Drifters Nine, Two Harbours, Lend Over, Gordon Pellworth, Barons of Teme, Rafters, Q7, Marble Owls and many more.

Poster needs our website address.
www.thebandbrisk.example.co.uk

Poster needs our Agent Name and number

Represented by- ORV - 01632 960418

Target Market(s)

Holiday Parks
Hotels
Nightclubs
Bars

Industry/Entity Type

Landscape

Colors
000000

Requirements
Must have
• Can be Portrait or Landscape. Poster could be Black and White or Colour
A very creative Logo

www.thebandbrisk.example.co.uk

Nice to have
• Cool, Contemopoary, Modern design
Photos can be cut out or changed in anyway to make us look great.

```html
<!DOCTYPE html>
<html lang="en">
<head>
<meta charset="utf-8">
<title>Brisk – The Band</title>
<link rel="stylesheet" href="https://fonts.googleapis.com/css2?family=Arimo:wght@400&family=Saira+Condensed:wght@600&display=swap">
<style>
  :root {
    --page: #ffffff;
    --card-light: #a9a9a9;
    --card-mid: #8a8a8a;
    --card-dark: #5e5e5e;
    --card-deep: #4a4a4a;
    --ink-white: #ffffff;
    --ink-dark: #111111;
    --wordmark: #1c1c1c;
    --accent: #e2521c;
    --strip-light: rgba(255,255,255,0.55);
    --strip-fade: rgba(255,255,255,0.12);
  }
  * { margin: 0; padding: 0; box-sizing: border-box; }
  html, body {
    width: 1200px;
    height: 1200px;
    overflow: hidden;
    background: var(--page);
  }
  .poster {
    position: absolute;
    left: 130px;
    top: 303px;
    width: 965px;
    height: 624px;
    overflow: hidden;
    background:
      radial-gradient(ellipse 60% 55% at 35% 40%, var(--card-light) 0%, rgba(169,169,169,0) 70%),
      radial-gradient(ellipse 50% 45% at 70% 25%, #9c9c9c 0%, rgba(156,156,156,0) 70%),
      linear-gradient(160deg, var(--card-mid) 0%, var(--card-dark) 60%, var(--card-deep) 100%);
    font-family: "Arimo", Arial, sans-serif;
  }
  .contact {
    position: absolute;
    right: 55px;
    top: 50px;
    text-align: right;
    color: var(--ink-white);
  }
  .contact__web {
    font-size: 30px;
    line-height: 38px;
  }
  .contact__agent {
    font-size: 21px;
    line-height: 28px;
    margin-top: 10px;
  }
  .logo {
    position: absolute;
    left: 100px;
    right: 0;
    top: 183px;
    display: flex;
    justify-content: center;
    align-items: baseline;
    gap: 12px;
    font-family: "Saira Condensed", "Arial Narrow", sans-serif;
    font-weight: 600;
  }
  .logo__name {
    font-size: 290px;
    line-height: 1;
    letter-spacing: 4px;
    font-weight: 600;
    color: var(--wordmark);
  }
  .logo__tag {
    font-size: 30px;
    line-height: 1;
    color: var(--accent);
    white-space: nowrap;
  }
  .setlist {
    position: absolute;
    left: 0;
    top: 499px;
    width: 965px;
    height: 90px;
    padding: 8px 40px 0 20px;
    background: linear-gradient(90deg, var(--strip-light) 0%, rgba(255,255,255,0.35) 45%, var(--strip-fade) 100%);
    color: var(--ink-dark);
    font-size: 22px;
    line-height: 38px;
    text-align: center;
  }
</style>
</head>
<body>
  <main class="poster">
    <div class="contact">
      <p class="contact__web">www.thebandbrisk.example.co.uk</p>
      <p class="contact__agent">Represented by- ORV - 01632 960418</p>
    </div>

    <div class="logo">
      <h1 class="logo__name">BRISK</h1>
      <p class="logo__tag">The Band</p>
    </div>

    <p class="setlist">Performing hits by - The Drifters Nine, Two Harbours, Lend Over, Gordon Pellworth,<br>Barons of Teme, Rafters, Q7, Marble Owls and many more.</p>
  </main>
</body>
</html>
```